Wine Bottle Label for Tall Fern Wines

We are a small, newly established winery in need of an original, bold and outstanding bottle label design for our Tall Fern wine.

Our vineyard and winery are located on a 200 acre farm in a remote part of southern Oregon. The name "Tall Fern" was inspired by the large, overgrown size of all of the foliage here, including our grapevines. Things grow large and vigorous in Oregon! And everything is very lush and green. It is almost surreal or other-worldly, like the landscapes seen in the Keeper of The Stones movies, or the land of Quill. It is a place that makes you say "wow" with its epic, large scale, natural beauty.

The name "Tall Fern" also captures the essence of our wine. It is big in flavor, quality and color. Our first release is a Pinot Noir (red). Pinot Noir wines often are subtle in flavor and thin in their color. Our label should convey that our Pinot Noir is a much more robust, darker, heavier, meatier, more flavorful wine that is a lot more fun than an "ordinary" wine. At the same time, this wine is not cheap, and so nothing in the label should convey "bargain," "low price," or "cheapness." This is a fine wine with a sense of adventure. Be sure to convey "quality" with your design along with "big," "adventure" and "fun".

The label should appeal to a younger demographic, both male and female, between the ages of 21 and 35. It should be non-traditional and adventurous and suggest a pushing of boundaries and a breaking of rules. This Pinot Noir does not conform to the normal "limitations" of the variety, therefore the label should not conform. It should have an "organic" or "natural" or "agricultural" vibe, as opposed to something mechanical or technical. It should, however, be contemporary. Do not confuse "natural" or "organic" with being nostalgic or old school. Think "agri-hipsters."

The label should be designed to fit on a Burgundy-style wine bottle (photo attached for reference). (Note: All Pinot Noir and Chardonnay is bottled in Burgundy bottles, If you are not sure about the bottle shape you can go to a local store and compare the various bottles. Locate a bottle of Pinot Noir or Chardonnay or anything identified as a "Burgundy Wine," and it should be the correct bottle. The tall, skinny bottles used for Cabernet Sauvignon are NOT correct)). Please see the "Must Have" notes for more on the bottle.

In summary, the final project should be a wine bottle label design that conveys bigness, vastness, adventurous, non-traditional, high quality wine. A good tagline to keep in mind is "Living Large."

Target Market(s)

Young, hip, non-conformist wine drinkers aged 21-35 with a sense of adventure and an appreciation of quality.

Industry/Entity Type

School

Requirements
Must have
• *Must contain the words:

Tall Fern (the brand)
2013 Pinot Noir (the vintage year and variety)

*The label must be designed to fit a Burgundy-style wine bottle. A photo is attached for reference.

*Additionally, the label needs to fit on the lower, widest part of the bottle. The label will be printed on sticky paper and rolled onto the bottle with a machine. The machine cannot apply labels to the neck of the bottle. The maximum size of a label that will fit this space is 5.5 inches wide by 4.5 inches tall. You DO NOT have to fill ALL of this space or confine the label shape to a rectangle, but the label cannot exceed this size or it won't stick to the bottle properly. It will really help if you can put your hands on an actual bottle to see the logistics of applying the label. But if that is not possible, just do your best with the instructions you have. I am confident the winning design could be adjusted to fit the bottle, if necessary
Nice to have
• *Wine grape leaf or leaves.

*A concept I have been playing with is sunlight shining through leaves like light through a Marlowe lamp or a stained glass window. This is NOT a requirement for this label. However, if the concept inspires and idea, I would be most happy to see it.
Should not have
• IF a leaf or leaves are included in the design (not a requirement) they MUST be wine grapevine leafs and preferably leaves of the Pinot Noir vine. Do not use generic leaves or identifiable leaves such as oak leaves, maple leaves, or anything that looks like the Canadian flag or the Halden Ridge Ravens hockey logo. Reference the attached photos of wine grape leaves to see the correct leaf type. I am happy to email more photos upon request. These photos may be used in whole or in part in your design, however, a leaf from a photo is NOT a requirement, nor is the image of a leaf or leaves.

This label should NOT be designed for Bordeaux-style wine bottles (the tall, skinny ones).

```html
<!DOCTYPE html>
<html lang="en">
<head>
<meta charset="utf-8">
<title>Tall Fern Pinot Noir Label</title>
<link rel="stylesheet" href="https://fonts.googleapis.com/css2?family=Pinyon+Script&family=Cormorant+Garamond:wght@500&family=Roboto+Condensed:wght@300&display=swap">
<style>
  :root {
    --canvas: #ffffff;
    --gold: #c9a12b;
    --wine-deep: #4f0a1e;
    --wine: #9c1437;
    --magenta: #c8205e;
    --silver: #bdbdbd;
    --silver-soft: #a9a9a9;
  }
  html, body {
    margin: 0;
    padding: 0;
    width: 1200px;
    height: 900px;
    overflow: hidden;
    background: var(--canvas);
  }
  .canvas {
    position: relative;
    width: 1200px;
    height: 900px;
  }
  .label {
    position: absolute;
    left: 417px;
    top: 255px;
    width: 366px;
    height: 390px;
  }
  .label__shape {
    position: absolute;
    inset: 0;
    width: 366px;
    height: 390px;
  }
  .label__text {
    position: absolute;
    left: 0;
    width: 340px;
    margin: 0;
    text-align: center;
    color: var(--silver);
  }
  .brand {
    top: 150px;
    font-family: "Pinyon Script", cursive;
    font-size: 66px;
    line-height: 1;
    font-weight: 400;
  }
  .vintage {
    top: 238px;
    left: 20px;
    font-family: "Cormorant Garamond", serif;
    font-size: 11px;
    letter-spacing: 1px;
    color: var(--silver-soft);
  }
  .variety {
    top: 258px;
    left: 20px;
    font-family: "Cormorant Garamond", serif;
    font-weight: 500;
    font-size: 22px;
    letter-spacing: 5px;
  }
  .origin-intro {
    top: 295px;
    left: 20px;
    font-family: "Cormorant Garamond", serif;
    font-size: 9px;
    letter-spacing: 1px;
    color: var(--silver-soft);
  }
  .origin {
    top: 310px;
    left: 20px;
    font-family: "Pinyon Script", cursive;
    font-size: 26px;
    line-height: 1;
  }
  .volume {
    position: absolute;
    top: 362px;
    font-family: "Roboto Condensed", sans-serif;
    font-weight: 300;
    font-size: 14px;
    color: var(--silver);
    margin: 0;
  }
  .volume--alcohol { left: 18px; }
  .volume--size { left: 266px; }
</style>
</head>
<body>
<main class="canvas">
  <section class="label" aria-label="Tall Fern Pinot Noir bottle label">
    <svg class="label__shape" viewBox="0 0 366 390" xmlns="http://www.w3.org/2000/svg">
      <defs>
        <radialGradient id="wine-swirl" cx="0.45" cy="0.35" r="0.75">
          <stop offset="0" stop-color="var(--magenta)"/>
          <stop offset="0.45" stop-color="var(--wine)"/>
          <stop offset="1" stop-color="var(--wine-deep)"/>
        </radialGradient>
      </defs>
      <g class="label__backing" fill="var(--gold)">
        <path d="M250,22 C292,34 304,86 292,148 L268,148 Z"/>
        <path d="M282,390 L282,178 C282,152 306,138 328,138 C350,138 366,156 366,180 L366,390 Z"/>
        <rect x="0" y="320" width="366" height="70"/>
      </g>
      <path class="label__artwork" role="img" aria-label="Flowing painted swirl of deep red and magenta, like wine in motion"
        fill="url(#wine-swirl)"
        d="M0,348 L0,178 C0,76 66,0 148,0 C214,0 266,42 282,112 L288,150 C282,182 278,242 290,300 L298,346 C240,362 200,350 150,358 C92,366 40,340 0,348 Z"/>
    </svg>
    <h1 class="label__text brand">Tall Fern</h1>
    <p class="label__text vintage">2013</p>
    <p class="label__text variety">PINOT NOIR</p>
    <p class="label__text origin-intro">PRODUCT FROM</p>
    <p class="label__text origin">Southern Oregon</p>
    <p class="volume volume--alcohol">ALCOHOL 13.5% BY VOLUME</p>
    <p class="volume volume--size">750ML.</p>
  </section>
</main>
</body>
</html>
```